Modern Business Card

Modern professional business card with more than just logo and demographic info. Something memorable.

We are a trendy/modern chiropractic group with an emphasis on neurology, hence the minimalist-type brain logo. We want to convey that modern and technical aspect with professionalism and the elite nature of our practice environment.

```html
<!DOCTYPE html>
<html lang="en">
<head>
<meta charset="utf-8">
<title>Vantage Chiropractic — Business Card</title>
<link href="https://fonts.googleapis.com/css2?family=Cinzel:wght@500&family=Montserrat:wght@400;500&display=swap" rel="stylesheet">
<style>
  :root {
    --backdrop: #d9d9d9;
    --card-black: #151515;
    --card-white: #ffffff;
    --brand-blue: #4a80c2;
    --ink: #1d1d1d;
    --ink-soft: #444444;
    --white: #ffffff;
  }
  * { box-sizing: border-box; margin: 0; padding: 0; }
  html, body {
    width: 1200px; height: 930px; overflow: hidden;
    background: var(--backdrop);
  }
  .stage { position: relative; width: 1200px; height: 930px; }

  .card {
    position: absolute; left: 260px;
    width: 680px; height: 390px;
    border-radius: 26px; overflow: hidden;
    box-shadow: 0 6px 18px rgba(0,0,0,0.18);
  }
  .card--front { top: 55px; background: var(--card-black); }
  .card--back  { top: 485px; background: var(--card-white); }

  /* front */
  .front-brand {
    position: absolute; inset: 0;
    display: flex; align-items: center; justify-content: center; gap: 22px;
  }
  .front-brand__mark { width: 26px; height: 26px; background: var(--white); }
  .front-brand__name {
    font-family: "Cinzel", serif; font-weight: 500;
    color: var(--white); font-size: 44px; letter-spacing: 2px; line-height: 1.05;
  }
  .front-brand__name span { display: block; font-size: 30px; letter-spacing: 3px; }

  /* back */
  .back-brand {
    position: absolute; left: 48px; top: 52px;
    font-family: "Cinzel", serif; font-weight: 500; color: var(--ink);
    font-size: 30px; letter-spacing: 1px; line-height: 1.05;
  }
  .back-brand span { display: block; font-size: 21px; letter-spacing: 2px; }

  .accent-bar {
    position: absolute; left: 0; top: 196px;
    width: 14px; height: 62px; background: var(--brand-blue);
  }
  .contact { position: absolute; left: 48px; top: 180px; }
  .contact__name {
    font-family: "Cinzel", serif; font-weight: 500;
    color: var(--brand-blue); font-size: 24px; letter-spacing: 1px;
  }
  .contact__role, .contact__line {
    font-family: "Montserrat", sans-serif; color: var(--ink-soft);
    font-size: 16px; line-height: 1.55;
  }
  .contact__role { margin-bottom: 4px; }
  .contact__list { list-style: none; margin-top: 6px; }
  .contact__list li {
    display: flex; align-items: center; gap: 12px;
    font-family: "Montserrat", sans-serif; color: var(--ink-soft);
    font-size: 16px; line-height: 1.6;
  }
  .contact__list svg { width: 14px; height: 14px; flex: none; }
  .highlight { color: var(--brand-blue); }

  .brand-disc {
    position: absolute; right: 70px; top: 40px;
    width: 300px; height: 300px; border-radius: 50%;
    background: var(--brand-blue);
  }
</style>
</head>
<body>
<main class="stage">
  <section class="card card--front" aria-label="Card front">
    <div class="front-brand">
      <div class="front-brand__mark"></div>
      <div class="front-brand__name">VANTAGE<span>CHIROPRACTIC</span></div>
    </div>
  </section>

  <section class="card card--back" aria-label="Card back">
    <div class="back-brand">VANTAGE<span>CHIROPRACTIC</span></div>
    <div class="accent-bar"></div>
    <div class="contact">
      <h1 class="contact__name">MARK ELLISON</h1>
      <p class="contact__role">Director</p>
      <p class="contact__line">2187 Fernwood Lane</p>
      <p class="contact__line">Salem, OR 97301</p>
      <ul class="contact__list">
        <li>
          <svg viewBox="0 0 24 24" aria-hidden="true"><path fill="#4a80c2" d="M6.6 10.8a15 15 0 0 0 6.6 6.6l2.2-2.2a1 1 0 0 1 1-.25 11.4 11.4 0 0 0 3.6.57 1 1 0 0 1 1 1V20a1 1 0 0 1-1 1A17 17 0 0 1 3 4a1 1 0 0 1 1-1h3.5a1 1 0 0 1 1 1c0 1.25.2 2.45.57 3.57a1 1 0 0 1-.25 1z"/></svg>
          (555) 218-4760
        </li>
        <li>
          <svg viewBox="0 0 24 24" aria-hidden="true"><rect x="2.5" y="5" width="19" height="14" rx="1.5" fill="none" stroke="#4a80c2" stroke-width="2"/><path d="M3 6l9 7 9-7" fill="none" stroke="#4a80c2" stroke-width="2"/></svg>
          hello@vantagechiro.com
        </li>
        <li>
          <svg viewBox="0 0 24 24" aria-hidden="true"><circle cx="12" cy="12" r="9.5" fill="none" stroke="#4a80c2" stroke-width="2"/><path d="M2.5 12h19M12 2.5c3 3 3 16 0 19M12 2.5c-3 3-3 16 0 19" fill="none" stroke="#4a80c2" stroke-width="1.6"/></svg>
          <span>www.<span class="highlight">vantagechiro</span>.com</span>
        </li>
      </ul>
    </div>
    <div class="brand-disc"></div>
  </section>
</main>
</body>
</html>
```